Harborlane Products Flyer

Harborlane Lending Group, Inc.
Licensed Mortgage Company
Serving the DMV since 1997
"You open the Harborlane, we'll carry the load"
We specialize in...
FHA Loans
* Credit Scores as low as 500
* 203K Renovation Loans
Conventional Loans
* As little as 1% Down
* Bank Statement for Self-Employed
Investor Loans
* DSCR, & Fix & Flip
* Commercial & New Construction
Other Programs
* HELOCS & Reverse Mortgages
Call today for a free consultation
(800) 914-6027
www.harborlanehomeloans.com
NMLS #731860

```html
<!DOCTYPE html>
<html lang="en">
<head>
<meta charset="utf-8">
<title>Harborlane Products Flyer</title>
<link rel="stylesheet" href="https://fonts.googleapis.com/css2?family=Tinos:wght@400;700&family=Poppins:wght@400&family=Open+Sans:ital,wght@0,700;1,400&family=Oswald:wght@700&display=swap">
<style>
  :root {
    --backdrop: #bdbdbd;
    --paper: #efefed;
    --navy: #001820;
    --gold-light: #f2d7a9;
    --gold-mid: #dcb57a;
    --gold-deep: #c6975a;
    --gold-text: #d6ad6f;
    --white: #ffffff;
    --ink: #0c1a20;
    --tile: #4c4a3f;
    --tile-light: #5b5a50;
  }
  * { margin: 0; padding: 0; box-sizing: border-box; }
  html, body {
    width: 879px; height: 1200px; overflow: hidden;
    background: var(--backdrop);
  }
  .flyer-frame {
    position: absolute; left: 131px; top: 137px;
    width: 617px; height: 926px; overflow: hidden;
  }
  .flyer {
    position: absolute; left: 0; top: 0;
    width: 1160px; height: 1740px;
    transform: scale(0.5319); transform-origin: 0 0;
    background: var(--paper);
    font-family: "Poppins", sans-serif;
  }
  .hero-art { position: absolute; left: 0; top: 0; width: 1160px; height: 790px; }
  .brand {
    position: absolute; left: 725px; top: 130px; width: 360px;
    text-align: center;
  }
  .brand-dot {
    width: 46px; height: 46px; border-radius: 50%;
    background: var(--gold-text); margin: 0 auto 16px;
  }
  .brand-name {
    font-family: "Tinos", serif; font-weight: 700;
    color: var(--gold-text); font-size: 28px; line-height: 1.15;
    letter-spacing: 0.5px; white-space: nowrap;
  }
  .brand-tagline {
    margin-top: 18px;
    font-family: "Open Sans", sans-serif; font-weight: 700;
    color: var(--white); font-size: 16px; line-height: 19px; letter-spacing: 1px;
    white-space: nowrap;
  }
  .slogan { font-family: "Tinos", serif; font-weight: 400; position: absolute; white-space: nowrap; }
  .slogan.line-1 { left: 612px; top: 400px; font-size: 42px; color: var(--white); letter-spacing: 1px; }
  .slogan.line-2 { left: 668px; top: 455px; font-size: 58px; color: var(--gold-text); }
  .slogan.line-3 { left: 744px; top: 537px; font-size: 42px; color: var(--white); letter-spacing: 1px; }
  .slogan.line-4 { left: 808px; top: 590px; font-size: 62px; color: var(--gold-text); }
  .specialize-heading {
    position: absolute; left: 29px; top: 612px;
    font-family: "Tinos", serif; font-weight: 400; font-size: 54px; color: var(--ink);
    letter-spacing: 1px; white-space: nowrap;
  }
  .product-card {
    position: absolute; width: 543px; height: 217px;
    background: var(--navy);
  }
  .card-fha { left: 24px; top: 914px; }
  .card-conventional { left: 590px; top: 914px; }
  .card-investor { left: 24px; top: 1157px; }
  .card-other { left: 590px; top: 1157px; }
  .card-tiles {
    position: absolute; right: 14px; top: 11px;
    display: grid; grid-template-columns: 25px 25px; gap: 10px;
  }
  .card-tiles span { width: 25px; height: 25px; background: var(--tile); }
  .card-tiles span:nth-child(1), .card-tiles span:nth-child(2) { background: var(--tile-light); }
  .card-title {
    position: absolute; left: 45px; top: 40px;
    font-family: "Tinos", serif; font-weight: 400; font-size: 34px; color: var(--gold-text);
    letter-spacing: 0.5px; white-space: nowrap;
  }
  .card-list { position: absolute; left: 50px; top: 98px; list-style: none; }
  .card-list li {
    display: flex; align-items: center; height: 42px;
    font-size: 24px; color: var(--white); white-space: nowrap;
  }
  .bullet-icon { width: 15px; height: 15px; margin-right: 20px; flex: none; }
  .bottom-art { position: absolute; left: 0; top: 1500px; width: 1160px; height: 240px; }
  .cta-label {
    position: absolute; left: 24px; top: 1574px; width: 600px; text-align: center;
    font-family: "Tinos", serif; font-weight: 700; font-size: 26px; color: var(--ink);
    letter-spacing: 1px; white-space: nowrap;
  }
  .cta-phone {
    position: absolute; left: 24px; top: 1608px; width: 600px; text-align: center;
    font-family: "Oswald", sans-serif; font-weight: 700; font-size: 82px; line-height: 1.2;
    color: var(--ink); letter-spacing: -1px;
  }
  .contact-block {
    position: absolute; left: 690px; top: 1628px; width: 460px; text-align: center;
    font-family: "Open Sans", sans-serif; font-style: italic; font-size: 24px;
    line-height: 36px; color: var(--white);
  }
</style>
</head>
<body>
<div class="flyer-frame">
  <div class="flyer">
    <svg class="hero-art" viewBox="0 0 1160 790">
      <defs>
        <linearGradient id="goldFade" x1="0" y1="0" x2="0" y2="1">
          <stop offset="0" stop-color="#f2d7a9"/>
          <stop offset="0.55" stop-color="#dcb57a"/>
          <stop offset="1" stop-color="#c6975a"/>
        </linearGradient>
        <linearGradient id="photoTone" x1="0" y1="0" x2="0" y2="1">
          <stop offset="0" stop-color="#9b9a8c"/>
          <stop offset="0.6" stop-color="#6f7a5a"/>
          <stop offset="1" stop-color="#4f7a34"/>
        </linearGradient>
      </defs>
      <polygon role="img" aria-label="Photo of a happy family in front of their house holding a home for sale sign" points="0,0 694,0 459,494 0,494" fill="url(#photoTone)"/>
      <line x1="718" y1="0" x2="462" y2="494" stroke="#ffffff" stroke-width="2"/>
      <polygon points="742,14 1160,14 1160,748 500,748 490,494" fill="#f5cf8a"/>
      <polygon points="766,32 1160,32 1160,748 680,748 508,494" fill="#001820"/>
      <polygon points="680,748 700,748 684,778" fill="#1d4477"/>
      <polygon points="0,494 545,494 685,782 0,782" fill="url(#goldFade)"/>
      <polyline points="0,525 522,525 655,782" fill="none" stroke="#0c1a20" stroke-width="1.5"/>
    </svg>

    <div class="brand">
      <div class="brand-dot"></div>
      <div class="brand-name">HARBORLANE<br>LENDING GROUP, INC.</div>
      <div class="brand-tagline">LICENSED MORTGAGE COMPANY<br>SERVING THE DMV SINCE 1997</div>
    </div>

    <div class="slogan line-1">YOU OPEN THE</div>
    <div class="slogan line-2">HARBORLANE,</div>
    <div class="slogan line-3">WE'LL CARRY</div>
    <div class="slogan line-4">THE LOAD</div>

    <h2 class="specialize-heading">WE SPECIALIZE IN…</h2>

    <section class="product-card card-fha">
      <div class="card-tiles"><span></span><span></span><span></span><span></span></div>
      <h3 class="card-title">FHA LOANS</h3>
      <ul class="card-list">
        <li><svg class="bullet-icon" viewBox="0 0 15 15"><rect width="6" height="6" fill="#d6ad6f"/><rect x="9" width="6" height="6" fill="#d6ad6f"/><rect y="9" width="6" height="6" fill="#d6ad6f"/><rect x="9" y="9" width="6" height="6" fill="#d6ad6f"/></svg>Credit Scores as low as 500</li>
        <li><svg class="bullet-icon" viewBox="0 0 15 15"><rect width="6" height="6" fill="#d6ad6f"/><rect x="9" width="6" height="6" fill="#d6ad6f"/><rect y="9" width="6" height="6" fill="#d6ad6f"/><rect x="9" y="9" width="6" height="6" fill="#d6ad6f"/></svg>203K Renovation Loans</li>
      </ul>
    </section>

    <section class="product-card card-conventional">
      <div class="card-tiles"><span></span><span></span><span></span><span></span></div>
      <h3 class="card-title">CONVENTIONAL LOANS</h3>
      <ul class="card-list">
        <li><svg class="bullet-icon" viewBox="0 0 15 15"><rect width="6" height="6" fill="#d6ad6f"/><rect x="9" width="6" height="6" fill="#d6ad6f"/><rect y="9" width="6" height="6" fill="#d6ad6f"/><rect x="9" y="9" width="6" height="6" fill="#d6ad6f"/></svg>As little as 1% Down</li>
        <li><svg class="bullet-icon" viewBox="0 0 15 15"><rect width="6" height="6" fill="#d6ad6f"/><rect x="9" width="6" height="6" fill="#d6ad6f"/><rect y="9" width="6" height="6" fill="#d6ad6f"/><rect x="9" y="9" width="6" height="6" fill="#d6ad6f"/></svg>Bank Statement for Self-Employed</li>
      </ul>
    </section>

    <section class="product-card card-investor">
      <div class="card-tiles"><span></span><span></span><span></span><span></span></div>
      <h3 class="card-title">INVESTOR LOANS</h3>
      <ul class="card-list">
        <li><svg class="bullet-icon" viewBox="0 0 15 15"><rect width="6" height="6" fill="#d6ad6f"/><rect x="9" width="6" height="6" fill="#d6ad6f"/><rect y="9" width="6" height="6" fill="#d6ad6f"/><rect x="9" y="9" width="6" height="6" fill="#d6ad6f"/></svg>DSCR, &amp; Fix &amp; Flip</li>
        <li><svg class="bullet-icon" viewBox="0 0 15 15"><rect width="6" height="6" fill="#d6ad6f"/><rect x="9" width="6" height="6" fill="#d6ad6f"/><rect y="9" width="6" height="6" fill="#d6ad6f"/><rect x="9" y="9" width="6" height="6" fill="#d6ad6f"/></svg>Commercial &amp; New Construction</li>
      </ul>
    </section>

    <section class="product-card card-other">
      <div class="card-tiles"><span></span><span></span><span></span><span></span></div>
      <h3 class="card-title">OTHER PROGRAMS</h3>
      <ul class="card-list">
        <li><svg class="bullet-icon" viewBox="0 0 15 15"><rect width="6" height="6" fill="#d6ad6f"/><rect x="9" width="6" height="6" fill="#d6ad6f"/><rect y="9" width="6" height="6" fill="#d6ad6f"/><rect x="9" y="9" width="6" height="6" fill="#d6ad6f"/></svg>HELOCS &amp; Reverse Mortgages</li>
      </ul>
    </section>

    <svg class="bottom-art" viewBox="0 0 1160 240" aria-hidden="true">
      <defs>
        <linearGradient id="goldFadeBottom" x1="0" y1="0" x2="0" y2="1">
          <stop offset="0" stop-color="#f2d7a9"/>
          <stop offset="0.55" stop-color="#dcb57a"/>
          <stop offset="1" stop-color="#c6975a"/>
        </linearGradient>
      </defs>
      <polygon points="0,2 699,2 716,85 670,85 617,240 0,240" fill="url(#goldFadeBottom)"/>
      <polygon points="670,85 1160,85 1160,240 617,240" fill="#001820"/>
    </svg>

    <div class="cta-label">CALL TODAY FOR A FREE CONSULTATION</div>
    <div class="cta-phone">(800) 914-6027</div>
    <div class="contact-block">
      WWW.HARBORLANEHOMELOANS.COM<br>NMLS #731860
    </div>
  </div>
</div>
</body>
</html>
```